Marla’s Sandwich Corner Grand Opening Door Flyer

1. Project Title
• “Flyer Design for Sandwich Shop Grand Opening”
• Why it’s effective: Direct and to the point, highlighting the purpose of the design.

2. Project Description
• “We’re looking for a professional designer to create a vibrant and modern flyer for our sandwich shop, Marla’s Corner. The flyer should emphasize our handcrafted sandwiches, fresh-baked bread, and house-made meats. As a women & family-owned business, we want this aspect prominently displayed. The flyer should also include our logo, a ‘Grand Opening’ and our website: MarlasCorner.example. We want the design to be clean, bold, and visually appealing to attract customers. We also would like a QR code so they can scan to load of the website to order online, but also list it.
• Why it’s effective: Clear goals, modern style preference, and necessary details outlined.

3. Visual Style
• “Modern, bold, and clean design with bright, appetizing colors. Focus on high-quality imagery of sandwiches, sleek fonts, and an inviting layout.”
• Why it’s effective: Communicates the desired aesthetic and tone.

4. Key Details to Include
• Business Name: Marla’s Sandwich Corner
• Taglines:
“Women & Family Owned”
“Handcrafted Sandwiches Made with Love”
“Fresh Baked Bread”
“House-made Slow Roasted House Specialties”
“Gluten-Friendly”
“Vegan-Friendly”
“7:00am Fresh Daily Grounded Coffee and Breakfast”

• Call-to-Action: “Order Online at MarlasCorner.example”
• Placeholder for the logo.
• Size: 4.25 x 11 (Door Hanger)
• File Format: High-resolution PDF, JPEG, or PNG.
• Print-Ready: Include bleed margins and ensure print clarity.

6. Tone
• Friendly and professional. Highlighting that your business is women-owned adds a unique and personal touch vs deli meat shops. We are a gourmet sandwich shop, with fresh baked bread, house-made meats, with gluten and vegan options. Each sandwich is made with love.

Target Market(s)

Coffee drinkers for morning crowd and sandwiches for lunch

Industry/Entity Type

Sandwich Shop

Colors
EB3D1F
EC4F4E
F09395
F8D3D4
FCEDEE

Requirements
Must have
• See Description
Nice to have
• Use website to get a feel for color theme
Should not have
• NA

```html
<!DOCTYPE html>
<html lang="en">
<head>
<meta charset="utf-8">
<title>Marla’s Sandwich Corner – Grand Opening Door Hanger</title>
<link rel="stylesheet" href="https://fonts.googleapis.com/css2?family=Alfa+Slab+One&family=Poppins:wght@300;400;600;700&family=Yellowtail&display=swap">
<style>
  :root {
    --orange: #EB3D1F;
    --coral: #EC4F4E;
    --rose: #F09395;
    --blush: #F8D3D4;
    --cream: #FCEDEE;
    --charcoal: #3a3a3c;
    --white: #ffffff;
  }
  * { margin: 0; padding: 0; box-sizing: border-box; }
  html, body { width: 1200px; height: 1200px; overflow: hidden; }
  body { background: var(--cream); font-family: "Poppins", sans-serif; position: relative; }

  .door-hanger { position: absolute; left: 385px; top: 45px; width: 430px; height: 1110px; }
  .door-hanger__shape { position: absolute; inset: 0; width: 430px; height: 1110px; }
  .door-hanger > *:not(svg) { position: absolute; }

  .brand-name { left: 28px; top: 212px; font-family: "Poppins", sans-serif; font-weight: 700; font-size: 15px; color: var(--blush); }

  .headline-kicker { left: 0; right: 0; top: 250px; text-align: center; }
  .headline-kicker__grand { font-family: "Alfa Slab One", serif; font-size: 16px; color: var(--orange); vertical-align: 30px; margin-right: 4px; letter-spacing: 1px; }
  .headline-kicker__opening { font-family: "Yellowtail", cursive; font-size: 58px; color: var(--white); }

  .headline-name { left: 0; right: 0; top: 312px; text-align: center; font-family: "Alfa Slab One", serif; font-size: 80px; line-height: 1; color: var(--orange); letter-spacing: 1px; }

  .ribbon { left: 34px; top: 410px; width: 362px; height: 46px; background: var(--orange);
    clip-path: polygon(0 0, 100% 0, 95% 50%, 100% 100%, 0 100%, 5% 50%);
    display: flex; align-items: center; justify-content: center;
    font-family: "Alfa Slab One", serif; font-size: 24px; color: var(--white); letter-spacing: 1px; }

  .sandwich-photo { left: 55px; top: 478px; width: 320px; height: 190px; border-radius: 28px;
    background: radial-gradient(circle at 30% 55%, #e9b765 0 30%, transparent 31%),
                radial-gradient(circle at 72% 40%, #f0c987 0 26%, transparent 27%),
                linear-gradient(135deg, #d99a45, #7aa53b 45%, #d8453a 70%, #f2d7a8); }

  .hours { left: 40px; top: 692px; color: var(--white); }
  .hours__title { font-family: "Alfa Slab One", serif; font-size: 34px; line-height: 1.1; }
  .hours__days { font-family: "Alfa Slab One", serif; font-size: 20px; margin-top: 4px; }
  .hours__time { font-family: "Poppins", sans-serif; font-weight: 300; font-size: 20px; }
  .hours__closed { font-weight: 300; font-size: 15px; margin-top: 2px; }

  .divider { left: 40px; top: 794px; width: 300px; border-top: 2px dotted var(--blush); }

  .features { left: 40px; top: 806px; list-style: none; color: var(--white); font-weight: 600; font-size: 16px; line-height: 25px; }

  .coffee-pill { left: 22px; top: 966px; width: 386px; height: 36px; border-radius: 18px; background: var(--cream);
    display: flex; align-items: center; justify-content: center;
    color: var(--orange); font-weight: 700; font-size: 11.5px; text-transform: uppercase; letter-spacing: 0.2px; }

  .contact { top: 1026px; color: var(--white); width: 130px; }
  .contact--address { left: 24px; }
  .contact--phone { left: 156px; }
  .contact--online { left: 290px; }
  .contact__label { font-family: "Alfa Slab One", serif; font-size: 12px; letter-spacing: 0.5px; }
  .contact__label--light { font-family: "Poppins", sans-serif; font-weight: 400; font-size: 9px; letter-spacing: 1.5px; text-transform: uppercase; }
  .contact__text { font-size: 10px; font-weight: 300; line-height: 1.4; margin-top: 3px; }
  .contact__phone { font-family: "Poppins", sans-serif; font-weight: 700; font-size: 19px; line-height: 1.2; }
</style>
</head>
<body>
  <article class="door-hanger">
    <svg class="door-hanger__shape" viewBox="0 0 430 1110" aria-hidden="true">
      <path d="M0 0 H430 V1110 H0 V200 H138.3 A62 62 0 1 0 113.8 160 H0 Z" fill="var(--charcoal)"/>
      <path d="M0 600 Q215 545 430 572 V990 H0 Z" fill="var(--orange)"/>
    </svg>

    <div class="brand-name">Marla’s Corner</div>

    <div class="headline-kicker">
      <span class="headline-kicker__grand">GRAND</span><span class="headline-kicker__opening">Opening</span>
    </div>
    <h1 class="headline-name">MARLA’S</h1>
    <div class="ribbon">SANDWICH CORNER</div>

    <div class="sandwich-photo" role="img" aria-label="Photo of two toasted ham, cheese, lettuce and tomato sandwich halves"></div>

    <div class="hours">
      <div class="hours__title">OPEN HOURS</div>
      <div><span class="hours__days">MON - SAT</span> <span class="hours__time">7 AM – 03 PM</span></div>
      <div class="hours__closed">Sunday – Closed</div>
    </div>
    <div class="divider"></div>

    <ul class="features">
      <li>Gluten-Friendly</li>
      <li>Vegan-Friendly</li>
      <li>Fresh Baked Bread</li>
      <li>Women &amp; Family Owned</li>
      <li>Handcrafted Sandwiches Made with Love</li>
      <li>House-made Slow Roasted House Specialties</li>
    </ul>

    <div class="coffee-pill">7:00 AM Fresh Daily Grounded Coffee and Breakfast</div>

    <div class="contact contact--address">
      <div class="contact__label">OUR ADDRESS</div>
      <div class="contact__text">42 Maple Ave.,<br>Fairview NJ 07000</div>
    </div>
    <div class="contact contact--phone">
      <div class="contact__label--light">Call us for order</div>
      <div class="contact__phone">555-014-0270</div>
    </div>
    <div class="contact contact--online">
      <div class="contact__label">ONLINE ORDER</div>
      <div class="contact__text">MarlasCorner.example</div>
    </div>
  </article>
</body>
</html>
```